Home Remodeling company needs a business card design

we need a business card design for home remodeling company in hamilton county, indiana USA. we offers a wide range of construction services including whole house renovations, Design and Build Basements and Kitchen and Bathroom Remodeling . we would like to see designs for both site of business card that use the same color of the company logo and also including all information below :
1- Karim Feltous CEO / General Contractor
2- all company contacts Telephone numbers ( 1-888-DULOM-47 ) ( 317-555-0193) email address ( info@dulomhome.com) website ( www.dulomhome.com ) and social media logos (Facebook- twitter- google plus )
3- company logo
4- licensed . insured . bonded

```html
<!DOCTYPE html>
<html lang="en">
<head>
<meta charset="utf-8">
<title>Dulom – Business Card</title>
<link rel="stylesheet" href="https://fonts.googleapis.com/css2?family=Cabin:wght@400;500;700&display=swap">
<style>
  :root {
    --page-bg: #e9e4dc;
    --card-bg: #f3f2ef;
    --card-edge: #d9d6d0;
    --ink-dark: #2b2b2d;
    --ink-grey: #555658;
    --accent-red: #b3202a;
    --band-dark: #1c1c1e;
    --band-text: #f2eee6;
  }
  * { margin: 0; padding: 0; box-sizing: border-box; }
  html, body {
    width: 1200px; height: 969px; overflow: hidden;
    background: var(--page-bg);
    font-family: "Cabin", "Gill Sans", sans-serif;
  }
  .business-card {
    position: absolute; left: 100px; top: 200px;
    width: 1000px; height: 564px;
    background: var(--card-bg);
    border: 1px solid var(--card-edge);
    box-shadow: 0 10px 30px rgba(0,0,0,0.12);
    overflow: hidden;
  }
  .brand {
    position: absolute; left: 62px; top: 66px;
    display: flex; align-items: center; gap: 18px;
  }
  .brand-square {
    width: 22px; height: 22px; background: var(--ink-dark);
  }
  .brand-name {
    font-weight: 700; font-size: 72px; color: var(--ink-dark);
    letter-spacing: 3px; line-height: 1;
  }
  .contact-list {
    position: absolute; left: 60px; top: 356px;
    list-style: none;
  }
  .contact-item {
    display: flex; align-items: center; gap: 16px;
    font-size: 26px; color: var(--ink-grey); height: 39px;
  }
  .contact-item svg { width: 22px; height: 22px; fill: var(--ink-dark); flex: none; }
  .name-band {
    position: absolute; right: 0; top: 374px;
    width: 454px; height: 93px;
    background: var(--band-dark);
    clip-path: polygon(42px 0, 100% 0, 100% 100%, 0 100%);
  }
  .name-band::after {
    content: ""; position: absolute; right: 0; top: 0;
    width: 16px; height: 100%; background: var(--accent-red);
  }
  .person {
    position: absolute; right: 40px; top: 9px; text-align: right;
    color: var(--band-text); white-space: nowrap;
  }
  .person-name { font-size: 33px; font-weight: 500; line-height: 1.25; }
  .person-title { font-size: 26px; line-height: 1.3; }
</style>
</head>
<body>
  <section class="business-card">
    <div class="brand">
      <div class="brand-square"></div>
      <div class="brand-name">DULOM</div>
    </div>

    <ul class="contact-list">
      <li class="contact-item">
        <svg viewBox="0 0 24 24"><path d="M6.6 10.8a15.1 15.1 0 0 0 6.6 6.6l2.2-2.2c.3-.3.7-.4 1-.2 1.1.4 2.3.6 3.6.6.6 0 1 .4 1 1V20c0 .6-.4 1-1 1A17 17 0 0 1 3 4c0-.6.4-1 1-1h3.5c.6 0 1 .4 1 1 0 1.3.2 2.5.6 3.6.1.3 0 .7-.2 1z"/></svg>
        <span>1-888-DULOM-47</span>
      </li>
      <li class="contact-item">
        <svg viewBox="0 0 24 24"><path d="M7 1h10a2 2 0 0 1 2 2v18a2 2 0 0 1-2 2H7a2 2 0 0 1-2-2V3a2 2 0 0 1 2-2zm0 3v14h10V4zm5 15.2a1.3 1.3 0 1 0 0 2.6 1.3 1.3 0 0 0 0-2.6z"/></svg>
        <span>317-555-0193</span>
      </li>
      <li class="contact-item">
        <svg viewBox="0 0 24 24"><path d="M2 5h20v14H2zm2 2v.4l8 5.2 8-5.2V7zm0 2.8V17h16V9.8l-8 5.2z"/></svg>
        <span>info@dulomhome.com</span>
      </li>
      <li class="contact-item">
        <svg viewBox="0 0 24 24"><circle cx="12" cy="12" r="10"/><path d="M2 12h20M12 2c3 3 3 17 0 20M12 2c-3 3-3 17 0 20" stroke="#f3f2ef" stroke-width="1.4" fill="none"/></svg>
        <span>www.dulomhome.com</span>
      </li>
    </ul>

    <div class="name-band">
      <div class="person">
        <div class="person-name">Karim Feltous</div>
        <div class="person-title">CEO / General Contractor</div>
      </div>
    </div>
  </section>
</body>
</html>
```